Investor Slide Deck

Simple idea - take a model investor deck and build out a investor deck for K7V. I will complete the data, I need a template to work from within. I will attach a model investor deck and a blank K7V that I need built out to K7V. Use the K7V Pwrpt to build out the investor deck

```html
<!DOCTYPE html>
<html lang="en">
<head>
<meta charset="utf-8">
<title>K7V Investor Deck</title>
<link href="https://fonts.googleapis.com/css2?family=Poppins:wght@400;500;600;700&display=swap" rel="stylesheet">
<style>
:root{
  --navy:#0b2a36;
  --navy-2:#123b4a;
  --teal:#00a99d;
  --band:#1f6e8c;
  --orange:#ff5a0a;
  --yellow:#f7b928;
  --ink:#1d2b33;
  --muted:#4a5358;
  --page:#f0f0f1;
  --white:#ffffff;
}
*{box-sizing:border-box;margin:0;padding:0}
html,body{width:1105px;height:1200px;overflow:hidden;background:var(--page);font-family:'Poppins',sans-serif;color:var(--ink)}
.deck{position:relative;width:1105px;height:1200px}
.slide{position:absolute;width:804px;height:452px;overflow:hidden;background:var(--white);transform:scale(0.598);transform-origin:0 0}
.col-l{left:48.4px}.col-r{left:577.6px}
.row-1{top:27px}.row-2{top:311px}.row-3{top:597px}.row-4{top:882px}
.abs{position:absolute}
.heading{font-weight:500;font-size:32px;letter-spacing:2px;color:var(--navy);line-height:1;padding-left:14px;border-left:3px solid var(--band)}
.heading.light{color:var(--white);border-color:var(--band)}
.footer-band{position:absolute;left:0;bottom:0;width:804px;height:37px}
.brand{position:absolute;left:17px;bottom:7px;font-weight:700;font-size:21px;letter-spacing:1px;color:var(--navy)}
.brand.light{color:var(--white)}
.page-no{position:absolute;right:14px;bottom:9px;width:21px;height:21px;border-radius:50%;background:var(--yellow);color:var(--white);font-size:9px;font-weight:600;display:flex;align-items:center;justify-content:center}
.photo{position:absolute}
/* title */
.title-slide{background:var(--navy)}
.title-slide .bg{inset:0;background:linear-gradient(120deg,#0f3445 0%,#0b2a36 55%,#10303a 100%)}
.title-slide h1{position:absolute;left:21px;top:170px;font-weight:500;font-size:29px;line-height:1.25;letter-spacing:2px;color:var(--white)}
.title-slide .sub{position:absolute;left:21px;top:250px;font-size:18px;letter-spacing:1.5px;color:var(--yellow)}
/* products */
.product{position:absolute;top:83px;width:247px;height:315px;color:var(--white);padding:8px}
.product .shot{height:152px;border:6px solid var(--white)}
.product h3{font-weight:500;font-size:16px;letter-spacing:1px;line-height:1.2;margin:10px 0 8px}
.product ul{list-style:none}
.product li{font-size:7.6px;line-height:1.3;margin-bottom:6px;padding-left:14px;position:relative}
.product li::before{content:"";position:absolute;left:1px;top:1px;width:6px;height:3px;border-left:1.5px solid currentColor;border-bottom:1.5px solid currentColor;transform:rotate(-45deg)}
.p-teal{background:var(--teal)}.p-navy{background:var(--navy)}.p-orange{background:var(--orange)}
.p-navy .shot,.p-orange .shot{border:none}
/* problems */
.problem-card{position:absolute;top:155px;width:145px;height:232px;background:var(--white);border-radius:9px;text-align:center;padding:10px 9px;box-shadow:0 2px 6px rgba(0,0,0,.12)}
.problem-card svg{display:block;margin:4px auto 10px}
.problem-card h4{font-size:12.5px;font-weight:600;color:var(--navy);line-height:1.35;margin-bottom:6px}
.problem-card p{font-size:8.4px;line-height:1.55;color:var(--muted)}
/* services */
.svc{position:absolute;width:190px}
.svc h4{font-size:13px;font-weight:600;color:var(--navy);line-height:1.3;margin-bottom:5px}
.svc p{font-size:8.3px;line-height:1.95;color:var(--muted)}
.svc.left{text-align:right}
.dot{position:absolute;width:50px;height:50px;border-radius:50%;display:flex;align-items:center;justify-content:center}
/* solutions */
.sol-icon{position:absolute;left:11px;width:52px;height:52px;border-radius:50%;display:flex;align-items:center;justify-content:center}
.sol-text{position:absolute;left:84px;width:705px}
.sol-text h4{font-size:13px;font-weight:600;color:var(--navy);margin-bottom:3px}
.sol-text p{font-size:8.6px;line-height:1.55;color:var(--muted)}
/* business */
.bm{position:absolute;top:276px;width:360px;text-align:center}
.bm h4{font-size:15px;font-weight:500;letter-spacing:1px;color:var(--ink);line-height:1.3;margin-bottom:4px}
.bm p{font-size:11px;line-height:1.75;color:var(--muted)}
.ring-photo{position:absolute;width:176px;height:176px;border-radius:50%;border:5px solid var(--teal);padding:5px;background:var(--white)}
.ring-photo div{width:100%;height:100%;border-radius:50%}
/* fund */
.fund-sub{position:absolute;left:32px;top:182px;font-size:14px;font-weight:500;letter-spacing:.5px;color:var(--teal)}
.fund-text{position:absolute;left:32px;width:330px;font-size:11px;line-height:1.85;color:var(--muted)}
.pie-label{position:absolute;font-size:11px;font-weight:500;color:var(--ink);line-height:1.25}
.pie-label b{display:block;font-size:17px;font-weight:600}
/* thank you */
.thanks{background:var(--navy)}
.thanks h2{position:absolute;left:30px;top:62px;font-weight:500;font-size:34px;letter-spacing:2px;color:var(--white)}
.contact{position:absolute;left:76px;color:var(--white);font-size:12px;line-height:1.85}
.contact h5{font-size:15px;font-weight:600;color:var(--yellow);line-height:1.3}
.c-icon{position:absolute;left:29px;width:36px;height:36px;border-radius:50%;background:var(--teal);display:flex;align-items:center;justify-content:center}
.social{position:absolute;top:346px;width:36px;height:36px;border-radius:50%;background:var(--orange)}
</style>
</head>
<body>
<div class="deck">

<!-- 1 Title -->
<section class="slide title-slide col-l row-1">
  <div class="photo bg" role="img" aria-label="Dark tinted rows of solar panels in a field"></div>
  <svg class="abs" style="left:0;top:0" width="804" height="452" viewBox="0 0 804 452">
    <path d="M470 120 A190 190 0 0 1 740 100" fill="none" stroke="var(--teal)" stroke-width="9"/>
    <path d="M485 355 A190 190 0 0 0 745 370" fill="none" stroke="var(--teal)" stroke-width="9"/>
  </svg>
  <div class="photo" role="img" aria-label="Engineer in safety vest inspecting solar panels" style="left:425px;top:57px;width:340px;height:340px;border-radius:50%;background:linear-gradient(160deg,#b7c3cc 0%,#6e8391 40%,#35505e 70%,#5b6b3a 100%)"></div>
  <h1>COMPANY TITLE<br>PRESENTATION SLIDE</h1>
  <div class="sub">INVESTOR DECK, 2024</div>
</section>

<!-- 5 Products -->
<section class="slide col-r row-1">
  <div class="abs heading" style="left:252px;top:26px">OUR PRODUCTS</div>
  <div class="product p-teal" style="left:18px">
    <div class="shot" role="img" aria-label="Bi-facial solar module on mounting frame" style="background:linear-gradient(180deg,#f4f5f7,#d9dde3)"></div>
    <h3>BI-FACIAL SOLAR PV<br>MODULE</h3>
    <ul><li>High Module Efficiency</li><li>Positive Power Tolerance upto 5 Watt</li><li>100% EL + VI Testing with 3 Stages</li><li>Increased Shade Tolerance</li><li>Split Junction Box Improves Heat Dissipation</li></ul>
  </div>
  <div class="product p-navy" style="left:282px">
    <div class="shot" role="img" aria-label="House roof with solar panels and inverter" style="background:linear-gradient(180deg,#3d5a86,#8a9aa8 60%,#b7a58b)"></div>
    <h3>SINGLE PHASE GRID TIE<br>INVERTERS</h3>
    <ul><li>High AC/DC Ratio for Higher Yields</li><li>Compact and Lightweight for easy installation.</li><li>User Friendly Web and App based monitoring.</li><li>Multiple MPPT Design With IDA Technology (Intelligent Disturbance Algorithm).</li></ul>
  </div>
  <div class="product p-orange" style="left:545px">
    <div class="shot" role="img" aria-label="Grid tie inverter unit close-up" style="background:linear-gradient(160deg,#8d969c,#2b3238 60%,#5a6b7a)"></div>
    <h3>THREE PHASE GRID TIE<br>INVERTERS</h3>
    <ul><li>Efficiency Upto 98.9%</li><li>Frequency Drop Control Technology</li><li>User Friendly Web and App based monitoring.</li><li>Weather, Consumption, String Level Monitoring System.</li></ul>
  </div>
  <svg class="footer-band" viewBox="0 0 804 37"><polygon points="230,0 804,0 804,37 208,37" fill="var(--band)"/></svg>
  <div class="brand">K7V</div><div class="page-no">5</div>
</section>

<!-- 2 Problems -->
<section class="slide col-l row-2">
  <div class="photo" role="img" aria-label="Two standing solar panels" style="left:560px;top:30px;width:180px;height:230px;background:linear-gradient(180deg,#2c3e66,#1a2748)"></div>
  <svg class="abs" style="left:0;top:0" width="804" height="452" viewBox="0 0 804 452"><polygon points="0,0 510,0 355,415 0,415" fill="var(--navy)"/></svg>
  <div class="abs heading light" style="left:14px;top:28px">PROBLEMS</div>
  <p class="abs" style="left:33px;top:70px;width:410px;font-size:11.5px;line-height:1.75;color:var(--white)">Every year, the rise in prices of electricity is burning a hole in the pocket of consumers. Solar Power is a reliable solution,  but the industry is facing its own set of challenges.</p>
  <div class="problem-card" style="left:11px"><svg width="34" height="30" viewBox="0 0 34 30"><polygon points="17,1 33,29 1,29" fill="var(--teal)"/><rect x="15.5" y="10" width="3" height="10" fill="#fff"/><rect x="15.5" y="22" width="3" height="3" fill="#fff"/></svg><h4>Poor Quality<br>Components</h4><p>The use of low-quality solar panels and components in solar plant construction is impacting their efficiency and lifespan.</p></div>
  <div class="problem-card" style="left:170px"><svg width="30" height="30" viewBox="0 0 30 30"><path d="M4 4h6v13H4zM12 4h11l3 11h-8l1 9-3 2-4-10z" fill="none" stroke="var(--orange)" stroke-width="2.2" stroke-linejoin="round"/></svg><h4>Poor<br>Installation</h4><p>Solar plant installations demand precision; poor installation can lead to downtime, damage, and efficiency loss.</p></div>
  <div class="problem-card" style="left:329px"><svg width="26" height="30" viewBox="0 0 26 30"><path d="M2 2h15l7 7v19H2z" fill="none" stroke="var(--navy)" stroke-width="2.2"/><path d="M7 14h12M7 19h12M7 24h8" stroke="var(--navy)" stroke-width="2"/></svg><h4>Lack of<br>Awareness</h4><p>Limited awareness of government subsidies and inadequate financing options for high-cost solar plant purchases can lead to missed product benefits</p></div>
  <div class="problem-card" style="left:488px"><svg width="36" height="30" viewBox="0 0 36 30"><ellipse cx="14" cy="12" rx="12" ry="9" fill="none" stroke="var(--band)" stroke-width="2.2"/><path d="M22 20a11 8 0 0 0 10 5l-2-5a9 7 0 0 0-4-12" fill="none" stroke="var(--band)" stroke-width="2.2"/></svg><h4>Unreliable<br>Customer<br>and Warranty<br>Support</h4><p>Challenges in reaching timely support and clarifying warranty terms can result in customer frustration and self-reliance for issue resolution.</p></div>
  <div class="problem-card" style="left:646px"><svg width="32" height="30" viewBox="0 0 32 30"><path d="M2 2v26h28" fill="none" stroke="var(--yellow)" stroke-width="2.2"/><rect x="7" y="16" width="4" height="9" fill="var(--yellow)"/><rect x="14" y="10" width="4" height="15" fill="var(--yellow)"/><rect x="21" y="5" width="4" height="20" fill="var(--yellow)"/></svg><h4>Lack of<br>Transparency in<br>Pricing and<br>Performance</h4><p>Customers might encounter unexpected hidden costs during installation and lower energy generation than initially agreed upon.</p></div>
  <svg class="footer-band" viewBox="0 0 804 37"><polygon points="230,0 804,0 804,37 208,37" fill="var(--band)"/></svg>
  <div class="brand light">K7V</div><div class="page-no">2</div>
</section>

<!-- 6 Services -->
<section class="slide col-r row-2">
  <div class="abs heading" style="left:262px;top:24px">OUR SERVICES</div>
  <svg class="abs" style="left:0;top:0" width="804" height="452" viewBox="0 0 804 452">
    <path d="M280 170 A150 150 0 0 1 528 170" fill="none" stroke="var(--teal)" stroke-width="6"/>
    <path d="M280 305 A150 150 0 0 0 528 305" fill="none" stroke="var(--teal)" stroke-width="6"/>
  </svg>
  <div class="photo" role="img" aria-label="Two engineers in hard hats beside solar panels and a wind turbine" style="left:267px;top:100px;width:274px;height:274px;border-radius:50%;background:linear-gradient(180deg,#9fb9cf 0%,#c9d6df 40%,#47618a 70%,#2b3f66 100%)"></div>
  <div class="dot" style="left:216px;top:123px;background:var(--orange)"><svg width="22" height="24" viewBox="0 0 22 24"><circle cx="11" cy="9" r="8" fill="#fff"/><rect x="7" y="17" width="8" height="5" fill="#fff"/></svg></div>
  <div class="dot" style="left:216px;top:286px;background:var(--yellow)"><svg width="26" height="18" viewBox="0 0 26 18"><rect x="1" y="1" width="24" height="16" rx="2" fill="none" stroke="#fff" stroke-width="2"/><circle cx="13" cy="9" r="4" fill="#fff"/></svg></div>
  <div class="dot" style="left:537px;top:123px;background:var(--band)"><svg width="24" height="24" viewBox="0 0 24 24"><circle cx="6" cy="6" r="4" fill="none" stroke="#fff" stroke-width="2.5"/><circle cx="18" cy="18" r="4" fill="none" stroke="#fff" stroke-width="2.5"/><path d="M20 3L4 21" stroke="#fff" stroke-width="2.5"/></svg></div>
  <div class="dot" style="left:537px;top:286px;background:var(--navy)"><svg width="28" height="24" viewBox="0 0 28 24"><circle cx="10" cy="13" r="7" fill="none" stroke="#fff" stroke-width="4" stroke-dasharray="3 2.5"/><circle cx="21" cy="7" r="4" fill="none" stroke="#fff" stroke-width="3" stroke-dasharray="2 2"/></svg></div>
  <div class="svc left" style="left:14px;top:120px"><h4>EPC Solutions</h4><p>Get turnkey EPC solutions that cover engineering, procurement, and construction. We develop long-term solutions that have a direct impact on the environment. Take care of all your electricity requirements</p></div>
  <div class="svc left" style="left:14px;top:283px"><h4>Solar Financing</h4><p>With our assistance, you can finance the installation of solar panels and renewable energy. We locate the best source for you to apply for and obtain the best solar loans.</p></div>
  <div class="svc" style="left:602px;top:120px"><h4>Installation and<br>Commission</h4><p>With our 24/7 remote monitoring, you may install and run solar panels without worrying about performance issues. We offer complete solutions. We provide support for all the systems we install for you.</p></div>
  <div class="svc" style="left:602px;top:283px"><h4>Operation<br>and Maintenance</h4><p>Get expert advice on how to run the solar plant once it has been installed. To care for your system and maintain its proper operation, we adhere to all applicable rules.</p></div>
  <svg class="footer-band" viewBox="0 0 804 37"><polygon points="230,0 804,0 804,37 208,37" fill="var(--band)"/></svg>
  <div class="brand">K7V</div><div class="page-no">6</div>
</section>

<!-- 3 Solutions -->
<section class="slide col-l row-3">
  <div class="abs heading" style="left:12px;top:20px">SOLUTIONS</div>
  <div class="sol-icon" style="top:74px;background:var(--navy)"><svg width="22" height="22" viewBox="0 0 22 22"><circle cx="11" cy="11" r="7" fill="none" stroke="#fff" stroke-width="5" stroke-dasharray="3.5 2"/><circle cx="11" cy="11" r="2.5" fill="#fff"/></svg></div>
  <div class="sol-icon" style="top:140px;background:var(--yellow);color:#fff;font-size:24px;font-weight:600">$</div>
  <div class="sol-icon" style="top:207px;background:var(--band)"><svg width="22" height="22" viewBox="0 0 22 22"><rect x="2" y="4" width="18" height="16" rx="2" fill="#fff"/><rect x="2" y="4" width="18" height="4" fill="#fff"/><path d="M5 11h3M10 11h3M15 11h2M5 15h3M10 15h3M15 15h2" stroke="var(--band)" stroke-width="2"/></svg></div>
  <div class="sol-icon" style="top:272px;background:var(--orange)"><svg width="22" height="22" viewBox="0 0 22 22"><path d="M4 18L13 9" stroke="#fff" stroke-width="3.5" stroke-linecap="round"/><circle cx="15" cy="7" r="5" fill="none" stroke="#fff" stroke-width="2.5"/></svg></div>
  <div class="sol-icon" style="top:338px;background:var(--teal)"><svg width="22" height="22" viewBox="0 0 22 22"><circle cx="9" cy="9" r="6" fill="none" stroke="#fff" stroke-width="3"/><path d="M13.5 13.5L20 20" stroke="#fff" stroke-width="3.5" stroke-linecap="round"/></svg></div>
  <div class="sol-text" style="top:76px"><h4>Quality Components</h4><p>With a portfolio of 2500+ solar power plants, we excel in selecting technically compatible, premium components to guarantee long-term results, planning an automated facility for high-quality solar panels.</p></div>
  <div class="sol-text" style="top:141px"><h4>Awareness About Subsidies And Financing</h4><p>K7V Energy educates residential consumers about Central Government subsidies and collaborates with banks and NBFCs to facilitate solar financing for various client segments.</p></div>
  <div class="sol-text" style="top:207px"><h4>Dedicated Customer And Warranty Support</h4><p>K7V Energy's dedicated team offers comprehensive after-sales support, facilitating swift warranty-covered service at local offices for our Panels and Inverters, eliminating brand-related delays.</p></div>
  <div class="sol-text" style="top:272px"><h4>Efficient Installation</h4><p>Our proficient design and site engineers create solar plants to precise technical specs, ensuring low-maintenance  installations with a flawless track record of zero system failures.</p></div>
  <div class="sol-text" style="top:338px"><h4>Transparent Pricing &amp; Performance</h4><p>We ensure transparent pricing and performance commitments in our projects. Our designs are created with the shadow analysis of solar panels for optimum result. We also provide the projected power generation and payback report of solar plant using software</p></div>
  <svg class="footer-band" viewBox="0 0 804 37"><polygon points="230,0 804,0 804,37 208,37" fill="var(--band)"/></svg>
  <div class="brand">K7V</div><div class="page-no">3</div>
</section>

<!-- 7 Business model -->
<section class="slide col-r row-3">
  <div class="abs heading" style="left:236px;top:20px">BUSINESS MODEL</div>
  <div class="ring-photo" style="left:117px;top:85px"><div role="img" aria-label="Tilted solar panels against the sky" style="background:linear-gradient(200deg,#dfe7ee,#6f87a8 55%,#22395e)"></div></div>
  <div class="ring-photo" style="left:510px;top:85px"><div role="img" aria-label="Large solar farm seen from above" style="background:linear-gradient(180deg,#b9c9d8,#4b6a9a 45%,#2a4275)"></div></div>
  <div class="bm" style="left:25px"><h4>SALES OF SOLAR PANEL</h4><p>Solar Panels manufactured at our manufacturing facility will be sold via different channels that we will develop. We aim to reach out to B2C customers via a separate franchise model that we will begin after commencement of manufacturing operations.</p></div>
  <div class="bm" style="left:418px"><h4>GOVERNMENT AND INDUSTRIAL<br>EPC PROJECTSEL</h4><p>We project about half of our manufactured solar panels to be used in EPC projects that we will bid for. We aim to generate gross margins of 10% - 12% on the overall projects.</p></div>
  <svg class="footer-band" viewBox="0 0 804 37"><polygon points="230,0 804,0 804,37 208,37" fill="var(--band)"/></svg>
  <div class="brand">K7V</div><div class="page-no">7</div>
</section>

<!-- 4 Fund raise -->
<section class="slide col-l row-4">
  <div class="abs heading" style="left:12px;top:125px">FUND RAISE</div>
  <div class="fund-sub">COMPANY NAME ENERGY IS RAISING:</div>
  <p class="fund-text" style="top:202px">Total Funding – ₹122Cr INR ($14.5 Mn) to build and start operations of a solar panel manufacturing plant in India.</p>
  <p class="fund-text" style="top:282px">We are looking to raise capital in a 65% Equity and 35% Debt ratio.</p>
  <svg class="abs" style="left:471px;top:93px" width="264" height="264" viewBox="0 0 264 264">
    <g transform="rotate(-90 132 132)" fill="none" stroke-width="64">
      <circle cx="132" cy="132" r="100" stroke="var(--navy)" stroke-dasharray="628.3 0"/>
      <circle cx="132" cy="132" r="100" stroke="var(--orange)" stroke-dasharray="12.6 628.3"/>
      <circle cx="132" cy="132" r="100" stroke="var(--yellow)" stroke-dasharray="0 12.6 12.6 628.3"/>
      <circle cx="132" cy="132" r="100" stroke="var(--band)" stroke-dasharray="0 25.2 238.8 628.3"/>
    </g>
    <circle cx="132" cy="132" r="67" fill="#fff"/>
    <circle cx="115" cy="116" r="5" fill="var(--yellow)"/>
    <polygon points="118,148 132,122 152,122 140,148" fill="#3b82d6"/>
    <path d="M138 148v10M130 158h16" stroke="#9aa4ab" stroke-width="2"/>
  </svg>
  <div class="pie-label" style="left:590px;top:45px;text-align:center"><b style="color:var(--orange)">2%</b>Payroll</div>
  <div class="pie-label" style="left:649px;top:52px"><b style="color:var(--yellow)">2%</b>Startup Expenses</div>
  <div class="pie-label" style="left:734px;top:140px"><b style="color:var(--band)">38%</b>CAPEX</div>
  <div class="pie-label" style="left:408px;top:218px"><b style="color:var(--band)">58%</b>Working<br>Capital</div>
  <svg class="footer-band" viewBox="0 0 804 37"><polygon points="230,0 804,0 804,37 208,37" fill="var(--band)"/></svg>
  <div class="brand">K7V</div><div class="page-no">4</div>
</section>

<!-- 10 Thank you -->
<section class="slide thanks col-r row-4">
  <svg class="abs" style="left:0;top:0" width="804" height="452" viewBox="0 0 804 452">
    <path d="M535 27 H773 a12 12 0 0 1 12 12 V250 H535z" fill="var(--yellow)"/>
    <path d="M353 190 V410 a12 12 0 0 0 12 12 H605 V190z" fill="var(--teal)"/>
  </svg>
  <div class="photo" role="img" aria-label="Solar farm rows beside green crops under a bright sky" style="left:363px;top:35px;width:414px;height:380px;border-radius:18px;background:linear-gradient(180deg,#dfe3e2 0%,#8ea0ab 30%,#2f4a6c 55%,#2f5a2a 75%,#1e3a1a 100%)"></div>
  <h2>THANK YOU</h2>
  <div class="c-icon" style="top:127px"><svg width="16" height="14" viewBox="0 0 16 14"><path d="M1 2l4.5-1.5 5 1.5 4.5-1.5v11.5l-4.5 1.5-5-1.5L1 13.5z" fill="#fff"/></svg></div>
  <div class="contact" style="top:122px"><h5>Address</h5>48 Harrow Lane Suite 210,<br>Brookfield 20415, United State</div>
  <div class="c-icon" style="top:214px"><svg width="16" height="14" viewBox="0 0 16 14"><path d="M1 2l4.5-1.5 5 1.5 4.5-1.5v11.5l-4.5 1.5-5-1.5L1 13.5z" fill="#fff"/></svg></div>
  <div class="contact" style="top:209px"><h5>Phone No</h5>+100-555-0147</div>
  <div class="c-icon" style="top:278px"><svg width="16" height="12" viewBox="0 0 16 12"><rect width="16" height="12" rx="1.5" fill="#fff"/><path d="M1 1l7 5.5L15 1" fill="none" stroke="var(--teal)" stroke-width="1.5"/></svg></div>
  <div class="contact" style="top:273px"><h5>Email</h5>hello@k7venergy.com</div>
  <div class="social" style="left:29px"></div>
  <div class="social" style="left:76px"></div>
  <div class="social" style="left:125px"></div>
</section>

</div>
</body>
</html>
```